Party Favors and Decorations Business Needs A Business Card Design

We are in need of a Logo design and business card design for a new small business called Bright Lantern Designs. We create party decorations and favours for Bridal Showers, Baby Showers, Weddings Birthdays etc. This is a very personalized service based on Clients theme, colour, and style. We are looking for a high end elegant look. I have attached a file to the style I like including the type of paper.

Target Market(s)

women, young adults, expectant mothers, mothers

Industry/Entity Type

Small Business

Contact Information for Business Card

Bright Lantern Designs Essex, ON 519-847-2061 brightlanterndesigns.ca karen@brightlanterngiftbox.com find us on Chatterly

Logo Text

Bright Lantern Designs

Font styles to use
Script

Requirements
Must have
• Name, email, web address, phone number
Should not have
• cutesy graphics

```html
<!DOCTYPE html>
<html lang="en">
<head>
<meta charset="utf-8">
<title>Bright Lantern Designs – Business Card</title>
<link href="https://fonts.googleapis.com/css2?family=Old+Standard+TT&family=Lobster+Two:wght@700&family=Open+Sans:wght@400;600;800&display=swap" rel="stylesheet">
<style>
  :root {
    --backdrop: #d9d4cc;
    --paper: #f7f7f5;
    --ink: #111111;
    --ink-soft: #3a3a3a;
    --rule: #9a9a9a;
    --night: #0b0b0b;
    --snow: #ffffff;
  }
  * { margin: 0; padding: 0; box-sizing: border-box; }
  html, body { width: 1200px; height: 885px; overflow: hidden; }
  body {
    background: var(--backdrop);
    position: relative;
    font-family: "Open Sans", sans-serif;
  }
  .card {
    position: absolute;
    left: 280px;
    width: 640px;
    height: 366px;
    box-shadow: 0 10px 28px rgba(0,0,0,.28);
    overflow: hidden;
  }
  .card--front { top: 50px; background: var(--paper); }
  .card--back { top: 469px; background: var(--night); }

  /* front */
  .front-body { position: absolute; inset: 0 0 68px 0; }
  .brand {
    position: absolute;
    font-family: "Old Standard TT", serif;
    line-height: 1.05;
    white-space: nowrap;
  }
  .brand__sub {
    display: block;
    font-family: "Open Sans", sans-serif;
    font-weight: 600;
    font-size: .5em;
    margin-top: 6px;
    letter-spacing: .3px;
  }
  .front-body .brand {
    left: 36px; top: 130px;
    color: var(--ink);
    font-size: 36px;
  }
  .divider {
    position: absolute;
    left: 300px; top: 34px; bottom: 34px;
    width: 1px; background: var(--rule);
  }
  .contact { position: absolute; left: 330px; top: 34px; color: var(--ink); }
  .contact__name {
    font-family: "Lobster Two", sans-serif;
    font-weight: 700;
    font-size: 30px;
    line-height: 1;
  }
  .contact__role { font-size: 14px; color: var(--ink-soft); margin-top: 4px; }
  .contact__list { list-style: none; margin-top: 22px; }
  .contact__item {
    display: flex; align-items: center; gap: 8px;
    font-size: 13px; margin-bottom: 6px; white-space: nowrap;
  }
  .icon { width: 13px; height: 13px; flex: none; }
  .social { display: flex; align-items: center; gap: 8px; margin-top: 14px; }
  .social__square { width: 28px; height: 28px; background: var(--ink); flex: none; }
  .social__text { line-height: 1; }
  .social__lead { font-size: 11px; font-weight: 600; display: block; }
  .social__name { font-size: 20px; font-weight: 800; display: block; }
  .address-band {
    position: absolute; left: 0; right: 0; bottom: 0; height: 68px;
    background: var(--night); color: var(--snow);
    display: flex; align-items: center; justify-content: center;
    font-size: 18px; font-weight: 600; letter-spacing: .3px;
    white-space: nowrap;
  }

  /* back */
  .card--back .brand {
    left: 250px; top: 70px;
    color: var(--snow);
    font-size: 52px;
  }
  .web {
    position: absolute; left: 60px; top: 290px;
    color: var(--snow); font-size: 22px; letter-spacing: .4px;
  }
</style>
</head>
<body>

<section class="card card--front" aria-label="Business card front">
  <div class="front-body">
    <div class="brand">Bright Lantern<span class="brand__sub">Designs</span></div>
    <div class="divider"></div>
    <div class="contact">
      <div class="contact__name">Employee Name</div>
      <div class="contact__role">Managing Director</div>
      <ul class="contact__list">
        <li class="contact__item">
          <svg class="icon" viewBox="0 0 13 13"><rect width="13" height="13" fill="#111"/><path d="M4 3l1.6 0 .6 2-1 .8c.5 1 1.2 1.7 2.2 2.2l.8-1 2 .6V10c-4 0-6.2-2.7-6.2-7z" fill="#fff"/></svg>
          519-847-2061
        </li>
        <li class="contact__item">
          <svg class="icon" viewBox="0 0 13 13"><rect width="13" height="13" fill="#111"/><circle cx="6.5" cy="6.5" r="3.8" fill="none" stroke="#fff" stroke-width="1"/><path d="M2.7 6.5h7.6M6.5 2.7v7.6" stroke="#fff" stroke-width=".8"/></svg>
          brightlanterndesigns.ca
        </li>
        <li class="contact__item">
          <svg class="icon" viewBox="0 0 13 13"><rect width="13" height="13" fill="#111"/><rect x="3" y="4" width="7" height="5" fill="none" stroke="#fff" stroke-width=".9"/><path d="M3 4l3.5 3 3.5-3" fill="none" stroke="#fff" stroke-width=".9"/></svg>
          karen@brightlanterngiftbox.com
        </li>
      </ul>
      <div class="social">
        <span class="social__square"></span>
        <span class="social__text"><span class="social__lead">Find us on</span><span class="social__name">Chatterly</span></span>
      </div>
    </div>
  </div>
  <div class="address-band">48 Maple Row S.Larkfield, LV,Z9Q 4K7,Northland</div>
</section>

<section class="card card--back" aria-label="Business card back">
  <div class="brand">Bright Lantern<span class="brand__sub">Designs</span></div>
  <div class="web">brightlanterndesigns.ca</div>
</section>

</body>
</html>
```